Create modern and sleek business card for luxury real estate company

We're a "boutique" real estate office looking for a design that gets across a highly modern luxury brand. Blacks and whites are probably the best colors unless we try a silver foil for the logo. I've attached a version of our current logo here. I'd like to swap out the current font on there with Gotham Light Regular.

I'm looking to have one side of the card have the logo with the space for our agents info on the other side.

Target Market(s)

Young professionals in a "luxury" headspace

Industry/Entity Type

Real estate

Contact Information for Business Card

A place for agent name, cell number, website. The slogan "Simply Rethinking Real Estate".

Font styles to use
Other font styles liked:
• Gotham Regular

Colors

Designer to choose only greyscale colors for use in the design.

Requirements
Must have
• Matte black as the background color. Clean lines and use of contrast. A specific design aspect that will use silver foil.
Nice to have
• Up in the air on integrating a QR code
Should not have
• Any houses or other real estate related design (ex: a clip art house)

```html
<!DOCTYPE html>
<html lang="en">
<head>
<meta charset="utf-8">
<title>Lumen Realty — Business Card</title>
<link href="https://fonts.googleapis.com/css2?family=Libre+Baskerville:wght@400;700&family=Arimo:wght@400&display=swap" rel="stylesheet">
<style>
  :root {
    --backdrop: #000000;
    --card: #2f3032;
    --card-edge: #3a3b3d;
    --ink: #f2f2f2;
    --ink-soft: #e4e4e4;
    --rule: #5a5b5e;
  }
  * { margin: 0; padding: 0; box-sizing: border-box; }
  html, body { width: 1200px; height: 900px; overflow: hidden; background: var(--backdrop); }
  .canvas { position: relative; width: 1200px; height: 900px; background: var(--backdrop); }

  .card {
    position: absolute;
    width: 458px;
    height: 282px;
    border-radius: 14px;
    background: linear-gradient(180deg, var(--card-edge) 0%, var(--card) 45%, #2a2b2d 100%);
    color: var(--ink);
    overflow: hidden;
  }
  .card--front { left: 138px; top: 265px; }
  .card--back { left: 625px; top: 269px; }

  .brand-mark {
    position: absolute;
    border: 2px solid var(--ink);
    border-radius: 50%;
  }
  .card--front .brand-mark { left: 94px; top: 78px; width: 60px; height: 60px; }
  .card--back .brand-mark { left: 88px; top: 99px; width: 80px; height: 80px; }

  .brand-name {
    position: absolute;
    font-family: "Libre Baskerville", serif;
    font-weight: 400;
    color: var(--ink);
    text-align: center;
    letter-spacing: 1px;
    line-height: 1.1;
  }
  .card--front .brand-name { left: 24px; width: 200px; top: 143px; font-size: 29px; }
  .card--back .brand-name { left: 188px; width: 172px; top: 100px; font-size: 36px; line-height: 1.2; }

  .divider {
    position: absolute;
    left: 220px; top: 53px;
    width: 1px; height: 162px;
    background: var(--rule);
  }

  .agent { position: absolute; left: 241px; top: 72px; width: 210px; }
  .agent__name {
    font-family: "Libre Baskerville", serif;
    font-weight: 700;
    font-size: 15px;
    letter-spacing: 0.5px;
    line-height: 19px;
  }
  .agent__title {
    font-family: "Arimo", sans-serif;
    font-size: 12.5px;
    color: var(--ink-soft);
    line-height: 16px;
  }
  .contact { list-style: none; margin-top: 12px; }
  .contact li {
    display: flex; align-items: center; gap: 5px;
    font-family: "Arimo", sans-serif;
    font-size: 12.5px;
    line-height: 17px;
    color: var(--ink);
  }
  .contact svg { width: 11px; height: 11px; flex: none; }
  .address {
    margin-top: 9px;
    font-family: "Arimo", sans-serif;
    font-size: 12.5px;
    line-height: 17px;
    font-style: normal;
    color: var(--ink);
  }
</style>
</head>
<body>
<main class="canvas">
  <section class="card card--front" aria-label="Business card, agent side">
    <span class="brand-mark" aria-hidden="true"></span>
    <p class="brand-name">LUMEN<br>REALTY</p>
    <span class="divider" aria-hidden="true"></span>
    <div class="agent">
      <h1 class="agent__name">DANIEL HART</h1>
      <p class="agent__title">Managing Director</p>
      <ul class="contact">
        <li>
          <svg viewBox="0 0 12 12" aria-hidden="true"><path d="M2.2 1h2l1 2.6-1.3.9a6.5 6.5 0 0 0 3.6 3.6l.9-1.3 2.6 1v2A1.2 1.2 0 0 1 9.8 11 8.8 8.8 0 0 1 1 2.2 1.2 1.2 0 0 1 2.2 1z" fill="none" stroke="#f2f2f2" stroke-width="1.1"/></svg>
          055-210 384 612
        </li>
        <li>
          <svg viewBox="0 0 12 12" aria-hidden="true"><rect x="0.8" y="2.2" width="10.4" height="7.6" fill="none" stroke="#f2f2f2" stroke-width="1.1"/><path d="M0.8 2.4 6 6.6l5.2-4.2" fill="none" stroke="#f2f2f2" stroke-width="1.1"/></svg>
          hello@lumenrealty.com
        </li>
        <li>
          <svg viewBox="0 0 12 12" aria-hidden="true"><circle cx="6" cy="6" r="5.1" fill="none" stroke="#f2f2f2" stroke-width="1"/><ellipse cx="6" cy="6" rx="2.2" ry="5.1" fill="none" stroke="#f2f2f2" stroke-width="0.9"/><path d="M1 6h10M1.8 3.4h8.4M1.8 8.6h8.4" stroke="#f2f2f2" stroke-width="0.9"/></svg>
          www.lumenrealty.com
        </li>
      </ul>
      <address class="address">88, Harbour View Lane<br>30718, Westbrook</address>
    </div>
  </section>

  <section class="card card--back" aria-label="Business card, brand side">
    <span class="brand-mark" aria-hidden="true"></span>
    <p class="brand-name">LUMEN<br>REALTY</p>
  </section>
</main>
</body>
</html>
```